BLS Business Card 2018

Larkmere Chiropractic. We have two locations that we want to advertise on the same card. Brightvale OrthoCore campus address: 3815 Pellham Dr., Suite 240, Flowood, MS 39417. Madison address: 246 Willowmere Dr., Building D., Madison, MS 39284. website: www.drlarkmere-example.com. o:(601)555-0147 f:(601)555-0183

Target Market(s)

Health care decision makers: primary care doctors and mothers

Contact Information for Business Card

I have no idea; up for any suggestions and I'd do much better picking from examples versus describing what I'm looking for. We are in a very high end location and would like the cards to look really sharp.

Requirements
Must have
• My name, Martin R Belvane, D.C.

```html
<!DOCTYPE html>
<html lang="en">
<head>
<meta charset="utf-8">
<title>Larkmere Chiropractic – Business Card</title>
<link href="https://fonts.googleapis.com/css2?family=Roboto:wght@400;500&family=Roboto+Condensed:wght@700&display=swap" rel="stylesheet">
<style>
  :root {
    --backdrop: #e9e6e2;
    --card: #f7f7f6;
    --ink: #111111;
    --text: #4a4a4a;
    --muted: #5a5a5a;
    --figure-light: #f2f2f2;
    --figure-mid: #cfcfcf;
    --figure-dark: #0a0a0a;
  }
  html, body {
    margin: 0;
    padding: 0;
    width: 1200px;
    height: 960px;
    overflow: hidden;
    background: var(--backdrop);
  }
  .stage {
    position: relative;
    width: 1200px;
    height: 960px;
  }
  .card {
    position: absolute;
    width: 600px;
    height: 343px;
    background: var(--card);
    box-shadow: 0 2px 4px rgba(0,0,0,0.25);
    overflow: hidden;
    font-family: "Roboto", Arial, sans-serif;
  }
  .card--front { left: 314px; top: 113px; }
  .card--back  { left: 311px; top: 472px; }

  .front__tab {
    position: absolute;
    left: 0; top: 50px;
    width: 12px; height: 40px;
    background: var(--ink);
  }
  .front__name {
    position: absolute;
    left: 37px; top: 56px;
    margin: 0;
    font-family: "Roboto Condensed", "Arial Narrow", sans-serif;
    font-weight: 700;
    font-size: 21px;
    letter-spacing: 0.2px;
    color: var(--ink);
  }
  .front__details {
    position: absolute;
    left: 37px; top: 123px;
    font-size: 14px;
    line-height: 18px;
    color: var(--text);
  }
  .address { margin: 0 0 7px; font-style: normal; }
  .contact { list-style: none; margin: 2px 0 0; padding: 0; }
  .contact li { display: flex; align-items: center; height: 20px; }
  .contact svg { width: 13px; height: 13px; margin-right: 10px; fill: var(--ink); }

  .front__figure {
    position: absolute;
    right: 0; top: 0;
    width: 275px; height: 343px;
    background: linear-gradient(100deg, var(--figure-light) 0%, var(--figure-mid) 60%, var(--figure-dark) 88%);
  }

  .back__brand {
    position: absolute;
    left: 0; right: 0; top: 130px;
    display: flex;
    justify-content: center;
    align-items: center;
    gap: 14px;
  }
  .back__mark {
    width: 14px; height: 14px;
    background: var(--ink);
  }
  .back__name {
    margin: 0;
    font-size: 34px;
    font-weight: 400;
    letter-spacing: 1px;
    text-transform: uppercase;
    color: var(--ink);
    line-height: 1;
  }
  .back__url {
    position: absolute;
    left: 0; right: 0; top: 282px;
    text-align: center;
    font-size: 14px;
    letter-spacing: 5px;
    color: var(--muted);
  }
</style>
</head>
<body>
<main class="stage">
  <section class="card card--front">
    <div class="front__tab"></div>
    <h1 class="front__name">MARTIN R BELVANE, D.C.</h1>
    <div class="front__details">
      <address class="address">Brightvale OrthoCore campus :<br>3815 Pellham Dr., Suite 240<br>Flowood, MS 39417.</address>
      <address class="address">Madison address:<br>246 Willowmere Dr., Building D.<br>Madison, MS 39284.</address>
      <ul class="contact">
        <li><svg viewBox="0 0 16 16" aria-hidden="true"><path d="M3.6 1.2l2.3 2.6-1.3 1.7c.9 2 2.4 3.5 4.4 4.4l1.7-1.3 2.6 2.3-1.4 2.5C6.5 13.2 2.8 9.5 1.1 2.6z"/></svg>(601)555-0147</li>
        <li><svg viewBox="0 0 16 16" aria-hidden="true"><path d="M4 1h8v4H4zM1 6h14v6h-3v3H4v-3H1zM5 10v4h6v-4z"/></svg>(601)555-0183</li>
        <li><svg viewBox="0 0 16 16" aria-hidden="true"><circle cx="8" cy="8" r="7"/><path d="M5 4c2 1 1 3 3 3s1 3 0 4M10 3c0 2 2 2 3 3" stroke="#f7f7f6" stroke-width="1.3" fill="none"/></svg>www.drlarkmere-example.com</li>
      </ul>
    </div>
    <div class="front__figure" role="img" aria-label="Line illustration of a muscular human torso with raised arm, set against a black edge"></div>
  </section>

  <section class="card card--back">
    <div class="back__brand">
      <span class="back__mark"></span>
      <p class="back__name">Larkmere Chiropractic</p>
    </div>
    <p class="back__url">WWW.DRLARKMERE-EXAMPLE.COM</p>
  </section>
</main>
</body>
</html>
```